Business Card Design

We are a law firm which provides services to creditors.....we do collection litigation. I am wide open on suggestions. I was thinking of a square card? Alternatively, a vertically oriented standard card or a folded card.....something unique. I would like to use my firm logo and beyond that, I am open for any and all suggestions. I'm uncertain if the complete log is uploaded? If not, please let me email it to you.

Industry/Entity Type

Law Firm

Contact Information for Business Card

Hart, Crane & Dobbs, P.C.
Tom Dobbs, Lawyer
4387 N Larkspur Ave
Oklahoma City, OK 73924
tdobbs@HcdCounsel.com
www.HcdCounsel.com
mobile: 405-382-7914

```html
<!DOCTYPE html>
<html lang="en">
<head>
<meta charset="utf-8">
<title>Hart, Crane &amp; Dobbs, P.C. — Business Card</title>
<link href="https://fonts.googleapis.com/css2?family=Arimo:wght@400;700&display=swap" rel="stylesheet">
<style>
  :root{
    --bg:#ecebe7;
    --card-white:#ffffff;
    --green:#14854a;
    --green-dark:#0b6b37;
    --green-light:#23a05e;
    --gold:#d4b24a;
    --ink:#4a4a4a;
    --ink-soft:#5c5c5c;
  }
  *{box-sizing:border-box;margin:0;padding:0}
  html,body{width:1200px;height:885px;overflow:hidden;background:var(--bg)}
  body{font-family:"Arimo",Arial,sans-serif;position:relative}
  .card{
    position:absolute;top:288px;width:540px;height:309px;border-radius:16px;
    box-shadow:0 6px 18px rgba(0,0,0,.18);overflow:hidden;
  }
  .card--front{left:40px;background:var(--card-white)}
  .card--back{left:620px;background:linear-gradient(135deg,var(--green-dark) 0%,var(--green) 55%,var(--green-light) 100%)}

  /* front */
  .brand-column{position:absolute;left:0;top:0;width:255px;height:100%;
    display:flex;flex-direction:column;align-items:center;justify-content:center;gap:18px}
  .brand-mark{width:74px;height:74px;border-radius:50%;background:var(--gold)}
  .brand-name{font-weight:700;font-size:19px;color:var(--ink);white-space:nowrap}
  .divider{position:absolute;left:262px;top:44px;width:1.5px;height:222px;background:var(--green)}
  .contact-column{position:absolute;left:288px;top:46px;right:20px}
  .person-name{font-weight:700;font-size:35px;color:var(--green);line-height:1}
  .person-title{font-weight:700;font-size:20px;color:var(--ink);margin-top:6px}
  .address{font-size:14.5px;color:var(--ink-soft);line-height:1.35;margin-top:22px}
  .contact-list{list-style:none;margin-top:14px}
  .contact-list li{display:flex;align-items:center;gap:8px;font-size:14.5px;color:var(--ink-soft);line-height:1.45}
  .contact-icon{width:15px;height:15px;flex:none}

  /* back */
  .back-content{position:absolute;inset:0;display:flex;flex-direction:column;align-items:center;justify-content:center}
  .back-brand{display:flex;align-items:center;gap:14px}
  .back-brand .brand-mark{width:58px;height:58px}
  .back-brand .brand-name{color:#fff;font-size:21px}
  .web-row{display:flex;align-items:center;gap:14px;margin-top:28px}
  .gold-rule{width:70px;height:1.5px;background:var(--gold)}
  .web{color:#fff;font-size:15px}
</style>
</head>
<body>
  <section class="card card--front" aria-label="Card front">
    <div class="brand-column">
      <div class="brand-mark" aria-hidden="true"></div>
      <div class="brand-name">Hart, Crane &amp; Dobbs, P.C.</div>
    </div>
    <div class="divider"></div>
    <div class="contact-column">
      <div class="person-name">Tom Dobbs</div>
      <div class="person-title">Lawyer</div>
      <p class="address">4387 N Larkspur Ave<br>Oklahoma City, OK 73924</p>
      <ul class="contact-list">
        <li>
          <svg class="contact-icon" viewBox="0 0 16 16" aria-hidden="true"><rect width="16" height="16" rx="3" fill="#14854a"/><rect x="5" y="3" width="6" height="10" rx="1" fill="none" stroke="#fff" stroke-width="1.4"/><circle cx="8" cy="11" r=".8" fill="#fff"/></svg>
          405-382-7914
        </li>
        <li>
          <svg class="contact-icon" viewBox="0 0 16 16" aria-hidden="true"><rect width="16" height="16" rx="3" fill="#14854a"/><rect x="3" y="4.5" width="10" height="7" fill="none" stroke="#fff" stroke-width="1.3"/><path d="M3 4.5 8 9 13 4.5" fill="none" stroke="#fff" stroke-width="1.3"/></svg>
          tdobbs@HcdCounsel.com
        </li>
        <li>
          <svg class="contact-icon" viewBox="0 0 16 16" aria-hidden="true"><rect width="16" height="16" rx="3" fill="#14854a"/><circle cx="8" cy="8" r="5" fill="none" stroke="#fff" stroke-width="1.2"/><ellipse cx="8" cy="8" rx="2.2" ry="5" fill="none" stroke="#fff" stroke-width="1"/><path d="M3 8h10" stroke="#fff" stroke-width="1"/></svg>
          www.HcdCounsel.com
        </li>
      </ul>
    </div>
  </section>

  <section class="card card--back" aria-label="Card back">
    <div class="back-content">
      <div class="back-brand">
        <div class="brand-mark" aria-hidden="true"></div>
        <div class="brand-name">Hart, Crane &amp; Dobbs, P.C.</div>
      </div>
      <div class="web-row">
        <span class="gold-rule"></span>
        <span class="web">www.HcdCounsel.com</span>
        <span class="gold-rule"></span>
      </div>
    </div>
  </section>
</body>
</html>
```